Brochure for a website accessibility report

This brochure is related to a report that www.qelvantrix.org sell. The report shows the results of an automated audit of a websites accessibility. It shows details of issues found with screen shots, examples of code and provides remediation advice.

The brochure will be a pdf 8.5 inches by 11 inches. It can be anywhere from 6 to 10 pages.

The FlintVue™ name itself should be “Bree Serif” font. The fonts, styles, colors and sizes are up to you.

The images used and logo of the Office of Digital Reachworks and K7P logo are upload

We highlighted in blue page extracts from the report we sell. Do not use the blue highlight, it is merely there to show you where the specific examples of the report we sell are vs the other content in the report. The areas in blue which show the content from the actual report should be shown as an extract of the actual page of the report. You have flexibility to change the layout and the way the content look.

The red square callouts over the blue content are callouts that describe the specific page extracts. We used it as a red callout only so that you would be able to see it. You should change the specific location, look and feel of the callout to be appropriate

Target Market(s)

Marketing and Technical people

Industry/Entity Type

Information Technology

Font styles to use
Sans Serif

Colors

Designer to choose colors to be used in the design.

Requirements
Should not have
• wheelchairs, images of blind people

```html
<!DOCTYPE html>
<html lang="en">
<head>
<meta charset="utf-8">
<title>Office of Digital Reachworks — Report Brochure Cover</title>
<link rel="stylesheet" href="https://fonts.googleapis.com/css?family=Bree+Serif&display=swap">
<style>
  :root {
    --backdrop: #a7a7ac;
    --cover-green: #2bb57a;
    --cover-green-light: #31bd81;
    --ink-white: #ffffff;
    --mark-dark: #3a3a3a;
  }

  html, body {
    margin: 0;
    padding: 0;
    width: 1200px;
    height: 913px;
    overflow: hidden;
    background: var(--backdrop);
  }

  .canvas {
    position: relative;
    width: 1200px;
    height: 913px;
  }

  .brochure-cover {
    position: absolute;
    left: 412px;
    top: 181px;
    width: 379px;
    height: 541px;
    background: linear-gradient(160deg, var(--cover-green-light) 0%, var(--cover-green) 100%);
    font-family: "Bree Serif", "Rockwell", "Roboto Slab", Georgia, serif;
    color: var(--ink-white);
  }

  .brand-square {
    position: absolute;
    left: 0;
    top: 250px;
    width: 48px;
    height: 48px;
    background: var(--mark-dark);
  }

  .brand-name {
    position: absolute;
    left: 82px;
    top: 243px;
    margin: 0;
    font-weight: 400;
    font-size: 20px;
    line-height: 21.6px;
    text-transform: uppercase;
    letter-spacing: 0;
    white-space: nowrap;
  }

  .report-title {
    position: absolute;
    left: 81px;
    top: 319px;
    margin: 0;
    font-weight: 400;
    font-size: 40px;
    line-height: 42px;
    letter-spacing: 0.06em;
    white-space: nowrap;
  }

  .report-byline {
    position: absolute;
    left: 83px;
    top: 364px;
    margin: 0;
    font-weight: 400;
    font-size: 7px;
    line-height: 8px;
    text-transform: uppercase;
    letter-spacing: 0.14em;
    white-space: nowrap;
  }
</style>
</head>
<body>
  <main class="canvas">
    <section class="brochure-cover" aria-label="Report brochure cover">
      <div class="brand-square" aria-hidden="true"></div>
      <p class="brand-name">Office of<br>Digital<br>Reachworks</p>
      <h1 class="report-title">REPORT</h1>
      <p class="report-byline">Office of Digital Reachworks</p>
    </section>
  </main>
</body>
</html>
```